A weight loss and fitness website design

I am into different types of modern weight loss techniques for people who are a little fatty and wish to be physically and mentally fit. Basically, the website is to teach people how to reduce weight using different methods such as diet, exercises, yoga and other forms. I would need an eye catching website which would make visitors want to come back. The will be also be different forms of exercises for a health and fit life. This said, my website is to have two categories of
1) weight loss techniques
2) exercise of fit and healthy living.
I prefer bright colors such as green, blue, yellow, and orange. Imagery should include before and after pictures of people suffering from obesity, people under going exercises.
Designers can get ideas and inspiration from the website fitlumen.com which i was previously part of the team.
Target Market(s)
My target audience are people suffering from obesity, malnutrition and physical deficiency.
Industry/Entity Type
Fitness
Coding
Coded - Design and coding required
Number of Pages Required
1 page
Look and feel

```html
<!DOCTYPE html>
<html lang="en">
<head>
<meta charset="utf-8">
<title>Kinetra Fitness</title>
<link href="https://fonts.googleapis.com/css2?family=Oswald:wght@400;500;600&family=Open+Sans:wght@400;600;700&display=swap" rel="stylesheet">
<style>
:root{
  --green:#8dc63f;
  --green-dark:#6fa92a;
  --blue:#3db8ee;
  --orange:#f7941d;
  --dark:#2d2f33;
  --darker:#1e1f22;
  --text:#555;
  --heading:#333;
  --light:#f2f2f2;
}
*{margin:0;padding:0;box-sizing:border-box}
html,body{width:1200px;height:3158px;overflow:hidden}
body{font-family:"Open Sans",sans-serif;color:var(--text);background:#fff;position:relative}
h1,h2,h3,h4{font-family:"Oswald",sans-serif;font-weight:500;color:var(--heading);text-transform:uppercase}
.accent{color:var(--green)}
p{font-size:12px;line-height:22px}
svg.ico{display:inline-block;vertical-align:middle;flex:none}

/* header */
.site-header{position:absolute;left:0;top:0;width:1200px;height:97px;background:var(--dark)}
.contact-tab{position:absolute;right:0;top:0;width:568px;height:42px;background:var(--green);color:#fff;font-size:13px;font-weight:700;display:flex;align-items:center;padding-left:34px;gap:26px;clip-path:polygon(18px 0,100% 0,100% 100%,0 100%)}
.contact-tab span{display:flex;align-items:center;gap:6px}
.brand{position:absolute;left:84px;top:28px;display:flex;align-items:center;gap:12px}
.brand-mark{width:38px;height:38px;border-radius:50%;background:var(--green)}
.brand-name{font-family:"Oswald",sans-serif;font-weight:600;font-size:26px;color:#fff;letter-spacing:1px;text-transform:uppercase}
.main-nav{position:absolute;top:62px;left:512px;display:flex}
.main-nav a{font-size:13px;font-weight:700;color:#fff;text-decoration:none;text-transform:uppercase;margin-right:40px}
.main-nav a.active{color:var(--green)}

/* hero */
.hero{position:absolute;top:97px;left:0;width:1200px;height:539px;background:linear-gradient(90deg,#ececec,#dedede)}
.hero-photo{position:absolute;right:0;top:0;width:560px;height:539px;background:radial-gradient(ellipse at 60% 45%,#c9a58c 0%,#b89a86 25%,#d8d6d4 60%,#e2e2e2 100%)}
.hero h1{position:absolute;left:86px;top:108px;font-size:70px;line-height:80px;font-weight:500}
.hero-text{position:absolute;left:86px;top:210px;width:520px;font-size:12px;line-height:25px;color:#444}
.btn{position:absolute;height:47px;display:flex;align-items:center;justify-content:center;color:#fff;font-size:13px;font-weight:700;text-transform:uppercase;border-radius:3px}
.btn-orange{background:var(--orange)}
.btn-green{background:var(--green)}
.slider-dots{position:absolute;left:558px;top:514px;display:flex;gap:6px}
.slider-dots span{width:11px;height:11px;border-radius:50%;border:2px solid #777}
.slider-dots span.on{background:var(--orange);border-color:var(--orange)}

/* plans */
.plan{position:absolute;top:678px;width:322px;height:347px;border-radius:3px;color:#fff;text-align:center;padding-top:20px}
.plan-green{left:86px;background:linear-gradient(#9bd24a,#79b52e)}
.plan-blue{left:438px;background:linear-gradient(#56c6f4,#22a4e0)}
.plan-orange{left:792px;background:linear-gradient(#fba13c,#f27c0c)}
.plan-icon{width:84px;height:84px;margin:0 auto;display:block}
.plan-figure{width:84px;height:84px;margin:0 auto;border-radius:50%;background:radial-gradient(circle,rgba(255,255,255,.85) 0 30%,rgba(255,255,255,.25) 31% 100%)}
.plan h3{color:#fff;font-size:25px;margin-top:26px}
.plan p{font-size:11px;line-height:21px;padding:8px 40px 0}
.plan-btn{display:inline-flex;align-items:center;gap:5px;margin-top:24px;border:2px solid #fff;padding:8px 10px;font-size:11px;font-weight:700;text-transform:uppercase}

/* section headings */
.sec-title{font-size:23px;line-height:30px}
.line-ornament{display:block;margin-top:8px}

/* weight loss */
.heart{position:absolute;left:95px;top:1080px;width:326px;height:290px;background:radial-gradient(ellipse at 50% 45%,#f0b449 0%,#9fcb54 35%,#e0764a 62%,#f7f7f7 80%)}
.weight-loss{position:absolute;left:450px;top:1090px;width:664px}
.weight-loss p{margin-top:14px;font-size:11.5px;line-height:26px}

/* exercise */
.exercise{position:absolute;top:1393px;left:0;width:1200px;height:464px;background:var(--darker)}
.exercise-photo{position:absolute;left:0;top:0;width:640px;height:464px;background:radial-gradient(ellipse at 55% 50%,#a0755a 0%,#5c4638 35%,#2a2a2c 70%,#1e1f22 100%)}
.exercise-body{position:absolute;left:663px;top:80px;width:470px}
.exercise-body h2{color:#fff;font-size:27px}
.exercise-body p{color:#ccc;font-size:11.5px;line-height:22px;margin-top:12px}
.exercise .btn{left:663px;top:352px;width:150px;height:42px}

/* people */
.people{position:absolute;left:86px;top:1910px;width:580px}
.people p{margin-top:16px;font-size:11.5px;line-height:24px}
.compare{position:absolute;left:701px;top:1911px;width:411px;height:274px;border:1px solid #ddd;background:#f5f5f5}
.compare-item{position:absolute;top:12px;width:185px;height:250px;border:1px solid #e2e2e2;background:linear-gradient(#fafafa 0%,#e8c8b0 35%,#4a4f66 65%,#f3f3f3 100%)}
.compare-tag{position:absolute;left:0;bottom:0;width:90px;height:30px;background:var(--green);color:#fff;font-weight:700;font-size:13px;display:flex;align-items:center;justify-content:center}

/* coaches */
.coaches{position:absolute;top:2227px;left:0;width:1200px;height:615px;background:linear-gradient(#f7f7f7,#eceae6)}
.coaches-head{position:absolute;top:62px;width:1200px;text-align:center}
.coaches-head p{width:680px;margin:14px auto 0;font-size:11px;line-height:22px}
.coach{position:absolute;top:211px;width:244px;height:337px;background:#fff;text-align:center;box-shadow:0 1px 3px rgba(0,0,0,.08)}
.coach-photo{width:244px;height:163px;background:linear-gradient(#d9cfc6,#a89282)}
.coach h4{font-size:17px;margin-top:20px}
.coach h4::after{content:"";display:block;width:36px;height:2px;background:var(--green);margin:6px auto 0}
.coach p{font-size:10.5px;line-height:19px;padding:8px 26px 0}
.coach-foot{position:absolute;left:0;bottom:0;width:100%;height:40px;border-top:1px solid #eee;display:flex;align-items:center;justify-content:space-between;padding:0 14px;font-size:11px}
.coach-foot .dots span{display:inline-block;width:8px;height:8px;border-radius:50%;background:#555;margin-right:5px}
.coach-foot .stars{color:#555;letter-spacing:1px}
.coach.featured{background:var(--green);color:#fff}
.coach.featured h4{color:#fff}
.coach.featured h4::after{background:#fff}
.coach.featured .coach-foot{border-color:rgba(255,255,255,.4)}
.coach.featured .dots span{background:#fff}
.coach.featured .stars{color:#fff}

/* footer */
.site-footer{position:absolute;top:2842px;left:0;width:1200px;height:248px;background:var(--dark);color:#ddd}
.footer-brand{position:absolute;left:86px;top:110px;display:flex;align-items:center;gap:12px}
.footer-col{position:absolute;top:42px}
.footer-col h4{color:#fff;font-size:17px}
.footer-col li{list-style:none;font-size:11px;line-height:16px;margin-top:12px;display:flex;gap:12px}
.footer-col li svg{margin-top:2px}
.footer-col p{font-size:11px;line-height:18px;margin-top:14px}
.input{width:224px;height:34px;background:#fff;color:#888;font-size:11px;padding:9px 12px;margin-top:12px}
.subscribe{display:inline-block;background:var(--green);color:#fff;font-size:10px;padding:6px 10px;margin-top:12px;text-transform:uppercase}
.social{display:flex;gap:8px;margin-top:18px}
.social span{width:34px;height:34px;border-radius:50%;border:2px solid #fff}
.copyright{position:absolute;top:3090px;left:0;width:1200px;height:68px;background:var(--green);color:#fff;font-size:12px;display:flex;align-items:center;justify-content:center}
</style>
</head>
<body>

<header class="site-header">
  <div class="contact-tab">
    <span><svg class="ico" width="12" height="12" viewBox="0 0 24 24"><path d="M6.6 10.8a15 15 0 0 0 6.6 6.6l2.2-2.2c.3-.3.7-.4 1-.2 1.1.4 2.3.6 3.6.6.6 0 1 .4 1 1V20c0 .6-.4 1-1 1A17 17 0 0 1 3 4c0-.6.4-1 1-1h3.5c.6 0 1 .4 1 1 0 1.3.2 2.5.6 3.6.1.3 0 .7-.2 1z" fill="#fff"/></svg>CALL US : (000)-555-0148</span>
    <span><svg class="ico" width="13" height="10" viewBox="0 0 26 20"><rect x="1" y="1" width="24" height="18" rx="2" fill="none" stroke="#fff" stroke-width="2.5"/><path d="M2 3l11 8 11-8" fill="none" stroke="#fff" stroke-width="2.5"/></svg>EMAIL : info@kinetrafitness.com</span>
  </div>
  <div class="brand"><span class="brand-mark"></span><span class="brand-name">Kinetra Fitness</span></div>
  <nav class="main-nav">
    <a class="active">Home</a><a>About Us</a><a>Classes</a><a>Trainers</a><a>Schedule</a><a>Contact Us</a>
  </nav>
</header>

<section class="hero">
  <div class="hero-photo" role="img" aria-label="Athletic woman crouching with dumbbells"></div>
  <h1>Kinetra <span class="accent">Fitness</span></h1>
  <p class="hero-text">Sed ut perspiciatis unde omnis iste natus error sit voluptatem accusantium doloremque laudantium, totam rem aperiam, eaque ipsa quae ab illo inventore veritatis et quasi architecto beatae vitae dicta sunt explicabo. Nemo enim ipsam voluptatem quia voluptas sit aspernatur aut odit aut fugit, sed quia consequuntur magni dolores.</p>
  <div class="btn btn-orange" style="left:86px;top:334px;width:169px">Read More Info</div>
  <div class="btn btn-green" style="left:261px;top:334px;width:169px">Join Us Now</div>
  <div class="slider-dots"><span></span><span></span><span class="on"></span><span></span><span></span></div>
</section>

<div class="plan plan-green">
  <svg class="plan-icon" viewBox="0 0 84 84" role="img" aria-label="Stopwatch icon"><circle cx="42" cy="48" r="26" fill="none" stroke="#fff" stroke-width="4"/><rect x="36" y="10" width="12" height="7" fill="#fff"/><line x1="42" y1="17" x2="42" y2="22" stroke="#fff" stroke-width="4"/><line x1="42" y1="48" x2="42" y2="32" stroke="#fff" stroke-width="4" stroke-linecap="round"/><line x1="42" y1="48" x2="54" y2="54" stroke="#fff" stroke-width="4" stroke-linecap="round"/><line x1="62" y1="24" x2="67" y2="19" stroke="#fff" stroke-width="4" stroke-linecap="round"/></svg>
  <h3>Diet Plan</h3>
  <p>Sed ut perspiciatis unde omnis iste natus error sit voluptatem accusantium doloremque laudantium, totam rem aperiam, eaque ipsa beatae vitae omnis iste dicta sunt explicabo.</p>
  <span class="plan-btn">Read More <svg class="ico" width="11" height="11" viewBox="0 0 12 12"><circle cx="6" cy="6" r="5" fill="none" stroke="#fff" stroke-width="1.5"/><path d="M5 3.5L7.5 6 5 8.5" fill="none" stroke="#fff" stroke-width="1.5"/></svg></span>
</div>
<div class="plan plan-blue">
  <div class="plan-figure" role="img" aria-label="Running figure icon"></div>
  <h3>Exercises Plan</h3>
  <p>Sed ut perspiciatis unde omnis iste natus error sit voluptatem accusantium doloremque laudantium, totam rem aperiam, eaque ipsa beatae vitae omnis iste dicta sunt explicabo.</p>
  <span class="plan-btn">Read More <svg class="ico" width="11" height="11" viewBox="0 0 12 12"><circle cx="6" cy="6" r="5" fill="none" stroke="#fff" stroke-width="1.5"/><path d="M5 3.5L7.5 6 5 8.5" fill="none" stroke="#fff" stroke-width="1.5"/></svg></span>
</div>
<div class="plan plan-orange">
  <div class="plan-figure" role="img" aria-label="Meditating figure icon"></div>
  <h3>Yoga Plan</h3>
  <p>Sed ut perspiciatis unde omnis iste natus error sit voluptatem accusantium doloremque laudantium, totam rem aperiam, eaque ipsa beatae vitae omnis iste dicta sunt explicabo.</p>
  <span class="plan-btn">Read More <svg class="ico" width="11" height="11" viewBox="0 0 12 12"><circle cx="6" cy="6" r="5" fill="none" stroke="#fff" stroke-width="1.5"/><path d="M5 3.5L7.5 6 5 8.5" fill="none" stroke="#fff" stroke-width="1.5"/></svg></span>
</div>

<div class="heart" role="img" aria-label="Heart shape made of fruits and vegetables"></div>
<section class="weight-loss">
  <h2 class="sec-title">Weight <span class="accent">Loss Techniques</span></h2>
  <svg class="line-ornament" width="70" height="10"><circle cx="5" cy="5" r="4" fill="none" stroke="#8dc63f" stroke-width="2"/><line x1="9" y1="5" x2="61" y2="5" stroke="#8dc63f" stroke-width="2"/><circle cx="65" cy="5" r="4" fill="none" stroke="#8dc63f" stroke-width="2"/></svg>
  <p>Sed ut perspiciatis unde omnis iste natus error sit voluptatem accusantium doloremque laudantium, totam rem aperiam, eaque ipsa quae ab illo inventore veritatis et quasi architecto beatae vitae dicta sunt explicabo. Nemo enim ipsam volupta tem quia voluptas sit aspernatur aut odit aut fugit, sed quia consequuntur magni dolores eos qui ratione voluptatem sequi perspiciatis unde omnis iste natus error sit voluptatem accusantium doloremque laudantium nesciunt.</p>
  <p>Neque porro quisquam est, qui dolorem ipsum quia dolor sit amet, consectetur, adipisci velit, sed quia non numquam eius modi tempora incidunt ut labore et dolore magnam aliquam quaerat voluptatem. Ut enim ad minima veni am, quis nostrum exercitationem ullam corporis suscipit laboriosam.</p>
</section>

<section class="exercise">
  <div class="exercise-photo" role="img" aria-label="Muscular man with towel and shaker beside a barbell"></div>
  <div class="exercise-body">
    <h2>Exercise of Fit &amp; <span class="accent">Healthy Living</span></h2>
    <svg class="line-ornament" width="70" height="10"><circle cx="5" cy="5" r="4" fill="none" stroke="#8dc63f" stroke-width="2"/><line x1="9" y1="5" x2="61" y2="5" stroke="#8dc63f" stroke-width="2"/><circle cx="65" cy="5" r="4" fill="none" stroke="#8dc63f" stroke-width="2"/></svg>
    <p>Sed ut perspiciatis unde omnis iste natus error sit voluptatem accusantium doloremque laudantium, totam rem aperiam, eaque ipsa quae ab illo inventore veritatis et quasi architecto beatae vitae dicta sunt explicabo nemo enim ipsam aut odit aut fugit, sed quia consequuntur magni dolores eos.</p>
    <p>At ratione voluptatem sequi nesciunt. Neque porro quisquam est, qui dolorem ipsum quia dolor sit amet, consectetur ut perspiciatis unde omnis iste natus error sit voluptatem accusa ntium</p>
  </div>
  <div class="btn btn-green">View More Here</div>
</section>

<section class="people">
  <h2 class="sec-title">People Under <span class="accent">Going Exercises</span></h2>
  <svg class="line-ornament" width="70" height="10"><circle cx="5" cy="5" r="4" fill="none" stroke="#8dc63f" stroke-width="2"/><line x1="9" y1="5" x2="61" y2="5" stroke="#8dc63f" stroke-width="2"/><circle cx="65" cy="5" r="4" fill="none" stroke="#8dc63f" stroke-width="2"/></svg>
  <p>Sed ut perspiciatis unde omnis iste natus error sit voluptatem accusantium doloremque laudantium, totam rem aperiam, eaque ipsa quae ab illo inventore veritatis et quasi architecto beatae vitae dicta sunt explicabo. Nemo enim ipsam volupta tem quia voluptas sit aspernatur aut odit aut fugit, sed quia consequuntur magni dolores accusantium doloremque laudantium nesciunt.</p>
  <p>Neque porro quisquam est, qui dolorem ipsum quia dolor sit amet, consectetur, adipisci velit, sed quia non numquam eius modi tempora incidunt ut labore et dolore magnam aliquam quaerat voluptatem. Ut enim ad minima veni am, quis nostrum exercitationem ullam corporis suscipit laboriosam</p>
</section>
<div class="compare">
  <div class="compare-item" style="left:12px" role="img" aria-label="Woman before weight loss"><span class="compare-tag">BEFORE</span></div>
  <div class="compare-item" style="left:212px" role="img" aria-label="Woman after weight loss"><span class="compare-tag">AFTER</span></div>
</div>

<section class="coaches">
  <div class="coaches-head">
    <h2 class="sec-title">Our <span class="accent">Fitness Coaches</span></h2>
    <svg class="line-ornament" width="70" height="10" style="margin:8px auto 0"><circle cx="5" cy="5" r="4" fill="none" stroke="#8dc63f" stroke-width="2"/><line x1="9" y1="5" x2="61" y2="5" stroke="#8dc63f" stroke-width="2"/><circle cx="65" cy="5" r="4" fill="none" stroke="#8dc63f" stroke-width="2"/></svg>
    <p>Sed ut perspiciatis unde omnis iste natus error sit voluptatem accusantium doloremque laudantium, totam rem aperiam eaque ipsa aut odit aut fugit, sed quia consequuntur magni dolores eos.</p>
  </div>
  <div class="coach featured" style="left:86px">
    <div class="coach-photo" style="background:linear-gradient(135deg,#e9ecef,#d4a88c 50%,#6aa7c9)" role="img" aria-label="Female coach holding a water bottle"></div>
    <h4>Coaches Name</h4>
    <p>Sed ut perspiciatis unde omnis iste nuvolu platem accusantium dolorem eaque ipsa qae aerror.</p>
    <div class="coach-foot"><span class="dots"><span></span><span></span><span></span><span></span></span><span class="stars">★★★★</span></div>
  </div>
  <div class="coach" style="left:347px">
    <div class="coach-photo" style="background:linear-gradient(135deg,#e6e6e6,#b88c72 50%,#9aa0a8)" role="img" aria-label="Two coaches in a gym"></div>
    <h4>Coaches Name</h4>
    <p>Sed ut perspiciatis unde omnis iste nuvolu platem accusantium dolorem eaque ipsa qae aerror.</p>
    <div class="coach-foot"><span class="dots"><span></span><span></span><span></span><span></span></span><span class="stars">★★★★</span></div>
  </div>
  <div class="coach" style="left:608px">
    <div class="coach-photo" style="background:radial-gradient(ellipse at 50% 60%,#b07a62,#3a2e2c 60%,#1d1d1d)" role="img" aria-label="Female coach with exercise ball"></div>
    <h4>Coaches Name</h4>
    <p>Sed ut perspiciatis unde omnis iste nuvolu platem accusantium dolorem eaque ipsa qae aerror.</p>
    <div class="coach-foot"><span class="dots"><span></span><span></span><span></span><span></span></span><span class="stars">★★★★</span></div>
  </div>
  <div class="coach" style="left:869px">
    <div class="coach-photo" style="background:linear-gradient(135deg,#dfe6d2,#d6b29a 50%,#9fbf88)" role="img" aria-label="Smiling female coach with towel"></div>
    <h4>Coaches Name</h4>
    <p>Sed ut perspiciatis unde omnis iste nuvolu platem accusantium dolorem eaque ipsa qae aerror.</p>
    <div class="coach-foot"><span class="dots"><span></span><span></span><span></span><span></span></span><span class="stars">★★★★</span></div>
  </div>
</section>

<footer class="site-footer">
  <div class="footer-brand"><span class="brand-mark"></span><span class="brand-name">Kinetra Fitness</span></div>
  <div class="footer-col" style="left:382px">
    <h4>Contact Us</h4>
    <ul>
      <li><svg class="ico" width="12" height="12" viewBox="0 0 24 24"><path d="M6.6 10.8a15 15 0 0 0 6.6 6.6l2.2-2.2c.3-.3.7-.4 1-.2 1.1.4 2.3.6 3.6.6.6 0 1 .4 1 1V20c0 .6-.4 1-1 1A17 17 0 0 1 3 4c0-.6.4-1 1-1h3.5c.6 0 1 .4 1 1 0 1.3.2 2.5.6 3.6.1.3 0 .7-.2 1z" fill="#ddd"/></svg>(000)-555-0148 (Phone)</li>
      <li><svg class="ico" width="12" height="12" viewBox="0 0 24 24"><rect x="6" y="2" width="12" height="6" fill="#ddd"/><rect x="2" y="9" width="20" height="10" rx="2" fill="#ddd"/><rect x="6" y="15" width="12" height="7" fill="#ddd" stroke="#2d2f33" stroke-width="1.5"/></svg>(000)-555-0149 (Fax)</li>
      <li><svg class="ico" width="12" height="12" viewBox="0 0 26 20"><rect x="1" y="1" width="24" height="18" rx="2" fill="#ddd"/><path d="M2 3l11 8 11-8" fill="none" stroke="#2d2f33" stroke-width="2.5"/></svg>hello@kinetrafitness.com</li>
      <li><svg class="ico" width="12" height="12" viewBox="0 0 24 24"><path d="M12 1a8 8 0 0 0-8 8c0 6 8 14 8 14s8-8 8-14a8 8 0 0 0-8-8zm0 11a3 3 0 1 1 0-6 3 3 0 0 1 0 6z" fill="#ddd"/></svg># 2514 Lorem Ipsum Dummy<br>Text Lorem Ipsum</li>
    </ul>
  </div>
  <div class="footer-col" style="left:635px;width:240px">
    <h4>Newsletter</h4>
    <p>Register Your email address to get information ablout us</p>
    <div class="input">Email Address</div>
    <span class="subscribe">Subscribe</span>
  </div>
  <div class="footer-col" style="left:905px;width:210px">
    <h4>Follow Us</h4>
    <p>Lorem ipsum dolor sit amet, conse ctetur adipiscing elit. Nulla in purus nibh. Donec ornare</p>
    <div class="social"><span></span><span></span><span></span><span></span><span></span></div>
  </div>
</footer>
<div class="copyright">&copy; Copyright 2016 Kinetra Fitness All Rights Reserved</div>

</body>
</html>
```